Counseling Practice Business Card

I need a professional looking business card incorporating my new logo that was just completed. Card needs to incorporate my name and title, description of my specialty, my address, my phone number, my fax number, my email and my website URL. I need to be able to choose design on/with different paper colors and textures.
I do not have a lot of business card ideas so I am open to anything but I want bold,sharp, clear card without additional designs other than my logo (see attached file info). I am open to different color backgrounds or paper colors including black. I do not like traditional brackets around area codes in phone number or dashes between numbers in phone number. Am open to other ways of presenting including periods between numbers as appropriate. I do not know enough to know what I like yet but I want card to coordinate and work together with my logo. My practice emphasizes natural mental health interventions so any use of color (with background paper color or the blue and green in my logo) that elicits nature is nice. In addition to black, any natural brown or wood looking background might be desirable also. Most of the offerings so far look very similar and boring.

Target Market(s)

Potential therapy clients and other professionals

Contact Information for Business Card

Card information:
Gerald M. Whitcombe, Ph.D.
Licensed Clinical Psychologist
Integrative Health Coach
4812 Marlowe Ridge Blvd SE
Suite 310
Duluth, GA 30096
(770) 415-2983 phone
(770) 581-4096 fax
drgeraldwhitcombe@quillmarsh.net
brightfernwellness.net

Font styles to use
Serif
Sans Serif
Other font styles liked:
• anything that you think looks crisp, clear and easily readable

Requirements
Must have
• Any color used should coordinate with my logo design (see attached files).
• Card should be printed horizontally so top and bottom are longest sides of rectangle.
• Background color or paper color should complement and highlight logo. Do not like a white background. black, grey, brown or any color my logo would blend well with.
Nice to have
• I would like designer to utilize color to highlight letters/name or phone-fax-web symbols.
• Bottom edge of card could be highlighted if appropriate to an idea.
Should not have
• I would NOT want the card to have a pure white background at all.
• No clear cards.
• Cards should be oriented with long sides on bottom and top, NOT sides. DO NOT LIKE THIS THIN TALL ORIENTATION.

```html
<!DOCTYPE html>
<html lang="en">
<head>
<meta charset="utf-8">
<title>Brightfern Wellness – Business Card</title>
<link href="https://fonts.googleapis.com/css2?family=Lato:wght@400;700;900&display=swap" rel="stylesheet">
<style>
  :root {
    --backdrop: #3a3c3f;
    --kraft: #d1b287;
    --kraft-light: #dcc099;
    --kraft-dark: #c6a67a;
    --leaf-green: #1d7a3a;
    --sky-blue: #2f74c0;
    --ink: #2a2620;
    --rule: #6b5d48;
  }
  * { box-sizing: border-box; margin: 0; padding: 0; }
  html, body {
    width: 1200px; height: 1200px; overflow: hidden;
    background: var(--backdrop);
    font-family: "Lato", sans-serif;
    color: var(--ink);
  }
  .canvas {
    width: 1200px; height: 1200px;
    display: flex; flex-direction: column; align-items: center; justify-content: center;
    gap: 44px;
  }
  .card {
    position: relative;
    width: 900px; height: 514px;
    border-radius: 40px;
    background: radial-gradient(ellipse at 30% 25%, var(--kraft-light), var(--kraft) 55%, var(--kraft-dark));
    overflow: hidden;
  }
  .brand {
    display: flex; align-items: center; gap: 18px;
    position: absolute;
  }
  .brand__dot {
    border-radius: 50%;
    background: var(--sky-blue);
    flex: none;
  }
  .brand__name {
    font-weight: 900;
    color: var(--leaf-green);
    letter-spacing: 0.5px;
    white-space: nowrap;
  }
  /* front */
  .card--front .brand { left: 50%; top: 50%; transform: translate(-50%, -50%); }
  .card--front .brand__dot { width: 62px; height: 62px; }
  .card--front .brand__name { font-size: 74px; }

  /* back */
  .card--back .brand { left: 48px; top: 318px; gap: 12px; }
  .card--back .brand__dot { width: 34px; height: 34px; }
  .card--back .brand__name { font-size: 38px; }

  .identity {
    position: absolute; left: 468px; top: 62px; width: 390px;
    padding-bottom: 14px;
    border-bottom: 1.5px solid var(--rule);
  }
  .identity__name {
    font-weight: 900; font-size: 25px; color: var(--leaf-green);
    text-transform: uppercase; letter-spacing: 0.2px;
  }
  .identity__name span { text-transform: none; }
  .identity__title { font-size: 19px; line-height: 1.3; margin-top: 4px; }

  .divider {
    position: absolute; left: 440px; top: 200px; width: 1.5px; height: 250px;
    background: var(--rule);
  }
  .contacts {
    position: absolute; left: 468px; top: 214px;
    list-style: none;
    font-size: 20px;
  }
  .contacts li { display: flex; align-items: flex-start; gap: 14px; line-height: 1.3; }
  .contacts li + li { margin-top: 12px; }
  .contacts .phones { margin-bottom: 6px; }
  .contacts .icon { width: 22px; height: 22px; flex: none; margin-top: 2px; fill: var(--sky-blue); }
  .contacts .stack { display: flex; flex-direction: column; gap: 4px; }
  .contacts .row { display: flex; gap: 14px; align-items: center; }
</style>
</head>
<body>
<main class="canvas">

  <section class="card card--front" aria-label="Card front">
    <div class="brand">
      <span class="brand__dot"></span>
      <span class="brand__name">Brightfern Wellness</span>
    </div>
  </section>

  <section class="card card--back" aria-label="Card back">
    <div class="brand">
      <span class="brand__dot"></span>
      <span class="brand__name">Brightfern Wellness</span>
    </div>

    <header class="identity">
      <h1 class="identity__name">Gerald M Whitcombe <span>Ph.D</span></h1>
      <p class="identity__title">Licensed Clinical Psychologist</p>
      <p class="identity__title">Integrative Health Coach</p>
    </header>

    <div class="divider"></div>

    <ul class="contacts">
      <li class="phones">
        <div class="stack">
          <div class="row">
            <svg class="icon" viewBox="0 0 24 24" aria-hidden="true"><path d="M6.6 10.8a15 15 0 0 0 6.6 6.6l2.2-2.2a1 1 0 0 1 1-.25 11.4 11.4 0 0 0 3.6.57 1 1 0 0 1 1 1V20a1 1 0 0 1-1 1A17 17 0 0 1 3 4a1 1 0 0 1 1-1h3.5a1 1 0 0 1 1 1c0 1.25.2 2.45.57 3.57a1 1 0 0 1-.25 1z"/></svg>
            <span>+770 . 415 . 2983</span>
          </div>
          <div class="row">
            <svg class="icon" viewBox="0 0 24 24" aria-hidden="true"><path d="M6 2h9l3 3v4H6zM4 10h16a2 2 0 0 1 2 2v6h-4v4H6v-4H2v-6a2 2 0 0 1 2-2zm4 6v4h8v-4z"/></svg>
            <span>+770 . 581 . 4096</span>
          </div>
        </div>
      </li>
      <li>
        <svg class="icon" viewBox="0 0 24 24" aria-hidden="true"><path d="M2 5h20v14H2zm2 2v.5l8 5 8-5V7zm0 2.8V17h16V9.8l-8 5z"/></svg>
        <span>drgeraldwhitcombe@quillmarsh.net</span>
      </li>
      <li>
        <svg class="icon" viewBox="0 0 24 24" aria-hidden="true"><path d="M12 2a10 10 0 1 0 0 20 10 10 0 0 0 0-20zm7.9 9h-3.4a15 15 0 0 0-1.3-6 8 8 0 0 1 4.7 6zM12 4c1 1.4 2.2 4 2.5 7h-5C9.8 8 11 5.4 12 4zM8.8 5a15 15 0 0 0-1.3 6H4.1a8 8 0 0 1 4.7-6zM4.1 13h3.4a15 15 0 0 0 1.3 6 8 8 0 0 1-4.7-6zM12 20c-1-1.4-2.2-4-2.5-7h5c-.3 3-1.5 5.6-2.5 7zm3.2-1a15 15 0 0 0 1.3-6h3.4a8 8 0 0 1-4.7 6z"/></svg>
        <span>www.brightfernwellness.net</span>
      </li>
      <li>
        <svg class="icon" viewBox="0 0 24 24" aria-hidden="true"><path d="M12 2a7 7 0 0 0-7 7c0 5 7 13 7 13s7-8 7-13a7 7 0 0 0-7-7zm0 9.5A2.5 2.5 0 1 1 12 6.5a2.5 2.5 0 0 1 0 5z"/></svg>
        <span>4812 Marlowe Ridge Blvd SE<br>Suite 310, Duluth, GA 30096</span>
      </li>
    </ul>
  </section>

</main>
</body>
</html>
```